House-share and Room Rental Website (With Focus on the Bedroom Landing Page)

Looking for website design for our House-share (executive accommodation) and room rental business.

Our company name is: Lodgivo could also be written as LodGivo or lodgivo. Either is fine .. just looking for a nice clean catchy logo to go with the design.

EXAMPLES
These are examples of other websites in this field that are doing well. this is a kind of baseline.
https://nestpartners-example.com.au/
https://www.bunkora-example.com/
https://www.dwelzy-example.com/
https://www.habiquo-example.net/
https://www.cohabiscout-example.com.au/

Our business model is to rent rooms to people looking for high-quality accommodation. We fill the gap between those looking to rent rooms and those with rooms to rent. However, our model is slightly different from those already on the market as we looking to fill a massive gap in the market delivering upmarket rooms for rent.(Executive Accommodation) also in the back end will be coupled with a self management process in the back end.

We offer executive style accommodation that stands out above the rest. With special extras like fire safety.. and management processes that create happier homes. We are looking for a web design package that can help us grow and scale our business. We need a design that is captivating

Our MAIN focus is having a room landing page that stands out from the rest... The core of our business will rely on the promotion of the rooms in a share house... so the whole design relies on the BEDROOM landing page to drive results.

Target Market(s)

We have 2 markets we are aiming at ... the first market is people offering rooms to rent who want the highest rental return. The second market is people looking to rent safe, high-quality rooms, in houses that are well managed and looked after.

Industry/Entity Type

Share Economy

Logo Text

LodGivo

Number of Pages Required

5+ page

Font styles to use
Sans Serif

Colors
3276b5

Requirements
Must have
• A messaging system whereby we can create direct communication between those offering rooms and those looking for rooms.
• A call to action that says " Schedule an Inspection"
• Landing page for promoting rooms
• A home page for showing stock.
• Profile page for those selling rooms
• Profile page for those looking for rooms.
• A scheduling calendar for booking inspections
Nice to have
• Pages where new residents can lock in a room.. pay bond and rents.. and sign contracts
• Notifications
• SMS capabilities in the backend.
Should not have
• No script or handwriting fonts.

```html
<!DOCTYPE html>
<html lang="en">
<head>
<meta charset="utf-8">
<title>Lodgivo — Room Rental</title>
<link rel="stylesheet" href="https://fonts.googleapis.com/css2?family=Montserrat:wght@400;500;600;700&family=Open+Sans:wght@400;600&display=swap">
<style>
:root{
  --brand:#3276b5;
  --brand-dark:#2c6aa4;
  --ink:#222;
  --muted:#777;
  --card-grey:#efefef;
  --bar-dark:#2b2b2b;
  --footer:#0b0b0b;
  --white:#fff;
}
*{box-sizing:border-box;margin:0;padding:0}
html,body{width:1200px;height:2908px;overflow:hidden}
body{font-family:"Montserrat",sans-serif;color:var(--ink);background:var(--white)}
a{color:inherit;text-decoration:none}

/* Header */
.site-header{height:103px;background:var(--brand);display:flex;align-items:center;padding:0 78px;position:relative}
.brand{display:flex;align-items:center;gap:14px;color:var(--white);font-weight:700;font-size:34px;letter-spacing:.5px}
.brand-dot{width:40px;height:40px;border-radius:50%;background:var(--white)}
.main-nav{display:flex;gap:34px;margin-left:auto;margin-right:42px}
.main-nav a{color:var(--white);font-size:14px;font-weight:500;letter-spacing:.3px;position:relative}
.main-nav a.active::before{content:"";position:absolute;left:0;top:-10px;width:18px;height:2px;background:var(--white)}
.btn-login{width:134px;height:45px;background:var(--white);color:var(--brand);font-weight:700;font-size:17px;display:flex;align-items:center;justify-content:center;letter-spacing:.5px}

/* Hero */
.hero{height:552px;position:relative;text-align:center;color:var(--white)}
.hero-photo{position:absolute;inset:0;background:linear-gradient(120deg,#5b5650 0%,#4a4640 35%,#6c665e 60%,#3d3a36 100%)}
.hero-photo::after{content:"";position:absolute;inset:0;background:rgba(20,20,20,.35)}
.hero-content{position:relative;padding-top:186px}
.hero h1{font-size:42px;font-weight:600;letter-spacing:.2px}
.hero p{font-size:17px;font-weight:500;margin-top:16px}
.search{display:flex;width:582px;height:52px;margin:26px auto 0}
.search input{flex:1;border:0;padding:0 22px;font:400 13px "Open Sans",sans-serif;color:#999}
.search button{width:134px;border:0;background:var(--brand);color:var(--white);font:700 15px "Montserrat",sans-serif;letter-spacing:.5px}

/* Intro + listings */
.intro{text-align:center;padding-top:90px}
.section-title{color:var(--brand);font-size:29px;font-weight:700;line-height:46px}
.intro-text{font:400 13px/25px "Open Sans",sans-serif;color:var(--muted);width:700px;margin:22px auto 0}
.listings{display:flex;gap:38px;justify-content:center;margin-top:52px}
.listing{width:324px}
.listing-photo{height:208px}
.p1{background:linear-gradient(135deg,#b8a794,#e0d8cc 55%,#8c7a66)}
.p2{background:linear-gradient(160deg,#6b5540,#c9a25a 50%,#e0b53a 70%,#7a6a55)}
.p3{background:linear-gradient(135deg,#e8e6e2,#cfd5da 50%,#9aa3ad)}
.listing-body{background:var(--card-grey);height:155px;text-align:center;padding-top:24px}
.listing-tag{font:400 13px "Open Sans",sans-serif;color:#666}
.listing-name{font-size:21px;color:#444;margin-top:18px}
.listing-price{font-size:19px;font-weight:700;color:var(--brand);margin-top:12px}
.listing-meta{height:41px;background:var(--bar-dark);display:flex;justify-content:space-between;align-items:center;padding:0 20px;color:var(--white);font-size:13px}
.listing-meta span{display:flex;align-items:center;gap:10px}
.listing-meta svg{width:26px;height:18px;stroke:var(--white);fill:none;stroke-width:1.4}

/* Rooms */
.rooms{background:var(--brand);margin-top:98px;height:1001px;color:var(--white);text-align:center;padding-top:42px}
.rooms h2{font-size:41px;font-weight:600}
.carousel{position:relative;height:372px;margin-top:32px}
.slide{position:absolute;top:0;height:372px}
.slide-left{left:0;width:229px;background:linear-gradient(135deg,#8a8684,#cfcac6 60%,#a8a39f)}
.slide-main{left:271px;width:656px;background:linear-gradient(150deg,#ececea,#d6d4d0 45%,#8e8a86 80%,#3a3836)}
.slide-right{right:0;width:230px;background:linear-gradient(135deg,#e9e7e2,#b49a7c 55%,#6a4a32)}
.slide-caption{position:absolute;right:38px;bottom:34px;text-align:right;color:var(--white)}
.slide-caption strong{display:block;font-size:24px;font-weight:500}
.slide-caption span{display:block;font-size:16px;margin-top:12px}
.tabs{display:flex;margin:90px 78px 0;border-bottom:1px solid rgba(255,255,255,.3);height:62px}
.tab{flex:1;font-size:17px;font-weight:500;text-align:center;position:relative}
.tab.active::after{content:"";position:absolute;left:0;right:0;bottom:-1px;height:2px;background:var(--white)}
.tab:first-child{flex:0 0 240px}
.info-grid{display:grid;grid-template-columns:253px 268px 269px 254px;margin:74px 78px 0}
.info-cell{height:104px;padding-top:16px;border-right:1px solid rgba(255,255,255,.3)}
.info-cell:nth-child(4n){border-right:0}
.info-cell:nth-child(-n+4){border-bottom:1px solid rgba(255,255,255,.3);height:103px}
.info-cell:nth-child(n+5){padding-top:40px}
.info-cell h3{font-size:17px;font-weight:400}
.info-cell p{font:400 13px "Open Sans",sans-serif;margin-top:16px}

/* CTA */
.cta{text-align:center;padding-top:56px;height:298px}
.cta .section-title{font-size:31px;line-height:46px}
.cta-actions{display:flex;gap:22px;justify-content:center;margin-top:36px}
.cta-actions a{width:207px;height:49px;background:var(--brand);color:var(--white);font-weight:700;font-size:17px;display:flex;align-items:center;justify-content:center;letter-spacing:.4px}

/* Footer */
.site-footer{background:var(--footer);height:157px;color:var(--white);text-align:center;padding-top:50px;font:400 13px "Open Sans",sans-serif}
.footer-nav{display:flex;justify-content:center;gap:0}
.footer-nav a{padding:0 28px;border-left:1px solid #777;line-height:14px}
.footer-nav a:first-child{border-left:0}
.copyright{margin-top:34px}
</style>
</head>
<body>

<header class="site-header">
  <a class="brand" href="#"><span class="brand-dot"></span>lodgivo</a>
  <nav class="main-nav">
    <a class="active" href="#">HOME</a>
    <a href="#">ROOMS</a>
    <a href="#">SELLERS</a>
    <a href="#">RENTORS</a>
    <a href="#">SCHEDULE AN INSPECTION</a>
  </nav>
  <a class="btn-login" href="#">LOGIN</a>
</header>

<section class="hero">
  <div class="hero-photo" role="img" aria-label="Photo of a bright bedroom with a bicycle and pillows on a bed"></div>
  <div class="hero-content">
    <h1>find your place with your life style</h1>
    <p>Lorem Ipsum is simply dummy text of the printing and typesetting industry.</p>
    <form class="search"><input type="text" placeholder="Enter City"><button type="button">SEARCH</button></form>
  </div>
</section>

<section class="intro">
  <h2 class="section-title">Lorem Ipsum is simply dummy text of the<br>printing and typesetting industry.</h2>
  <p class="intro-text">Lorem Ipsum is simply dummy text of the printing and typesetting industry. Lorem Ipsum has been the industry's standard dummy text ever since the 1500s, when an unknown printer took a galley of type and scrambled it to make a type specimen book. It has survived not only five centuries, but also the leap.</p>

  <div class="listings">
    <article class="listing">
      <div class="listing-photo p1" role="img" aria-label="Photo of a modern bedroom with wood panelling"></div>
      <div class="listing-body"><p class="listing-tag">Lorem Ipsum is simply.</p><h3 class="listing-name">Lorem Ipsum is simply.</h3><p class="listing-price">$ 230 981</p></div>
      <div class="listing-meta">
        <span><svg viewBox="0 0 26 18"><path d="M2 16V4M2 11h22v5M4 11V7h8v4M24 11V8a2 2 0 0 0-2-2h-8v5"/></svg>02</span>
        <span><svg viewBox="0 0 26 18"><path d="M2 8h22M4 8v4a4 4 0 0 0 4 4h10a4 4 0 0 0 4-4V8M6 16l-1 2M20 16l1 2M6 8V3h4"/></svg>01</span>
        <span><svg viewBox="0 0 26 18"><path d="M3 14V9l3-6h14l3 6v5zM3 9h20M6 12h2M18 12h2M5 14v3M21 14v3"/></svg>02</span>
      </div>
    </article>
    <article class="listing">
      <div class="listing-photo p2" role="img" aria-label="Photo of a hotel-style room with two beds and yellow throws"></div>
      <div class="listing-body"><p class="listing-tag">Lorem Ipsum is simply.</p><h3 class="listing-name">Lorem Ipsum is simply.</h3><p class="listing-price">$ 230 981</p></div>
      <div class="listing-meta">
        <span><svg viewBox="0 0 26 18"><path d="M2 16V4M2 11h22v5M4 11V7h8v4M24 11V8a2 2 0 0 0-2-2h-8v5"/></svg>02</span>
        <span><svg viewBox="0 0 26 18"><path d="M2 8h22M4 8v4a4 4 0 0 0 4 4h10a4 4 0 0 0 4-4V8M6 16l-1 2M20 16l1 2M6 8V3h4"/></svg>01</span>
        <span><svg viewBox="0 0 26 18"><path d="M3 14V9l3-6h14l3 6v5zM3 9h20M6 12h2M18 12h2M5 14v3M21 14v3"/></svg>02</span>
      </div>
    </article>
    <article class="listing">
      <div class="listing-photo p3" role="img" aria-label="Photo of a light studio room with a bed and grey sofa"></div>
      <div class="listing-body"><p class="listing-tag">Lorem Ipsum is simply.</p><h3 class="listing-name">Lorem Ipsum is simply.</h3><p class="listing-price">$ 230 981</p></div>
      <div class="listing-meta">
        <span><svg viewBox="0 0 26 18"><path d="M2 16V4M2 11h22v5M4 11V7h8v4M24 11V8a2 2 0 0 0-2-2h-8v5"/></svg>02</span>
        <span><svg viewBox="0 0 26 18"><path d="M2 8h22M4 8v4a4 4 0 0 0 4 4h10a4 4 0 0 0 4-4V8M6 16l-1 2M20 16l1 2M6 8V3h4"/></svg>01</span>
        <span><svg viewBox="0 0 26 18"><path d="M3 14V9l3-6h14l3 6v5zM3 9h20M6 12h2M18 12h2M5 14v3M21 14v3"/></svg>02</span>
      </div>
    </article>
  </div>
</section>

<section class="rooms">
  <h2>Rooms</h2>
  <div class="carousel">
    <div class="slide slide-left" role="img" aria-label="Photo of a grey bed with soft linen"></div>
    <div class="slide slide-main" role="img" aria-label="Photo of a bedroom with framed prints and a floor lamp">
      <div class="slide-caption"><strong>Lorem Ipsum.</strong><span>Lorem Ipsum is simply dummy text .</span></div>
    </div>
    <div class="slide slide-right" role="img" aria-label="Photo of a timber bedroom with a striped bedspread"></div>
  </div>

  <div class="tabs">
    <div class="tab active">GENERAL INFO</div>
    <div class="tab">CORE INFORMATION</div>
    <div class="tab">ROOM AMENITIES</div>
    <div class="tab">PUBLIC AMENITIES</div>
  </div>

  <div class="info-grid">
    <div class="info-cell"><h3>Gender Preference</h3><p>male/female</p></div>
    <div class="info-cell"><h3>Size of room</h3><p>40 Sqm</p></div>
    <div class="info-cell"><h3>Bathroom</h3><p>shared/private</p></div>
    <div class="info-cell"><h3>Parking</h3><p>street/off-street/private</p></div>
    <div class="info-cell"><h3>Smoking/non-smoking</h3><p>Smoking/non-smoking</p></div>
    <div class="info-cell"><h3>minimum contract ter</h3><p>usually 3 months</p></div>
    <div class="info-cell"><h3>Bed size</h3><p>male/female</p></div>
    <div class="info-cell"><h3>Gender Preference</h3><p>male/female</p></div>
  </div>
</section>

<section class="cta">
  <h2 class="section-title">Lorem Ipsum is simply dummy text of<br>the printing and typesetting.</h2>
  <div class="cta-actions"><a href="#">ROOM SELLERS</a><a href="#">RENTORS</a></div>
</section>

<footer class="site-footer">
  <nav class="footer-nav">
    <a href="#">Home</a><a href="#">Rooms</a><a href="#">Sellers</a><a href="#">Rentors</a><a href="#">Shedule an inspection</a>
  </nav>
  <p class="copyright">©lodgivo. 2019 - All Rights Reserved.</p>
</footer>

</body>
</html>
```